business card - Helicopter Flight Services, Flight School, etc.

We need a business card design for a new helicopter service.

We offer Helicopter Flight Services, Aerial Filming & Photography, Flight School, and Helicopter Tours. In that order.

Summit BladeAir, Inc.
Dennis Tollerby
SummitBladeair@Kestmail.com
626-418-7352

Based at the Brenwick Airport in Van Nuys, CA. The final design should communicate integrity and safety. Pictures or logos at your discretion.

Card back side - surprise me.

```html
<!DOCTYPE html>
<html lang="en">
<head>
<meta charset="utf-8">
<title>Summit BladeAir, Inc. — Business Card</title>
<link href="https://fonts.googleapis.com/css2?family=Source+Sans+3:wght@300;400&display=swap" rel="stylesheet">
<style>
  :root {
    --backdrop: #e4e2df;
    --card-white: #f7f7f7;
    --band-black: #151515;
    --ink-dark: #1c1c1c;
    --ink-light: #f2f2f2;
    --rule: #d8d8d8;
  }
  * { margin: 0; padding: 0; box-sizing: border-box; }
  html, body {
    width: 1200px; height: 892px; overflow: hidden;
    background: var(--backdrop);
    font-family: "Source Sans 3", "Myriad Pro", sans-serif;
  }
  .canvas {
    width: 1200px; height: 892px;
    display: flex; flex-direction: column;
    align-items: center; justify-content: center; gap: 44px;
  }
  .card {
    position: relative;
    width: 665px; height: 380px;
    background: var(--card-white);
    overflow: hidden;
    box-shadow: 0 2px 10px rgba(0,0,0,.12);
  }
  /* Front */
  .card-front .band { position: absolute; inset: 0; }
  .card-front .company {
    position: absolute; left: 200px; top: 46px;
    color: var(--ink-light); font-weight: 300; font-size: 40px; letter-spacing: .5px;
  }
  .card-front .title-rule {
    position: absolute; left: 150px; top: 112px; width: 430px; height: 1.5px;
    background: var(--ink-light);
  }
  .card-front .holder {
    position: absolute; left: 90px; top: 196px;
    color: #bdbdbd; font-weight: 300; font-size: 27px;
  }
  .card-front .divider {
    position: absolute; left: 318px; top: 176px; width: 1.5px; height: 130px;
    background: var(--ink-light);
  }
  .card-front .contact {
    position: absolute; left: 336px; top: 184px;
    list-style: none; color: var(--ink-light); font-size: 17px; line-height: 25px;
  }
  .card-front .contact li { display: flex; align-items: flex-start; gap: 9px; }
  .card-front .contact svg { flex: none; margin-top: 6px; }
  .card-front .contact .address { line-height: 21px; margin-top: 2px; }
  /* Back */
  .card-back .wordmark {
    position: absolute; left: 0; right: 0; top: 128px; text-align: center;
    color: var(--ink-dark); font-weight: 400; font-size: 62px; letter-spacing: .5px;
  }
  .card-back .services {
    position: absolute; left: 0; right: 0; top: 222px; text-align: center;
    color: var(--ink-dark); font-weight: 400; font-size: 27px;
  }
</style>
</head>
<body>
<main class="canvas">
  <section class="card card-front" aria-label="Card front">
    <svg class="band" width="665" height="380" viewBox="0 0 665 380" aria-hidden="true">
      <polygon points="110,0 665,0 665,300 555,380 0,380 0,80" fill="var(--band-black)"/>
    </svg>
    <h1 class="company">Summit BladeAir, Inc.</h1>
    <div class="title-rule"></div>
    <p class="holder">Dennis Tollerby</p>
    <div class="divider"></div>
    <ul class="contact">
      <li>
        <svg width="13" height="13" viewBox="0 0 13 13"><rect width="13" height="13" fill="#f2f2f2"/><path d="M4 2.5 L5.5 4.5 L4.8 5.6 C5.4 6.9 6.2 7.7 7.4 8.2 L8.5 7.5 L10.5 9 L9.6 10.5 C6 10.2 2.8 7 2.5 3.4 Z" fill="#151515"/></svg>
        <span>626-418-7352</span>
      </li>
      <li>
        <svg width="13" height="13" viewBox="0 0 13 13"><rect width="13" height="13" fill="#f2f2f2"/><rect x="2.5" y="3.5" width="8" height="6" fill="none" stroke="#151515" stroke-width="1.2"/><path d="M2.5 3.5 L6.5 7 L10.5 3.5" fill="none" stroke="#151515" stroke-width="1.2"/></svg>
        <span>SummitBladeair@Kestmail.com</span>
      </li>
      <li>
        <svg width="13" height="13" viewBox="0 0 13 13"><rect width="13" height="13" fill="#f2f2f2"/><path d="M2 6.5 L6.5 2.5 L11 6.5 L9.5 6.5 L9.5 10.5 L3.5 10.5 L3.5 6.5 Z" fill="#151515"/></svg>
        <span class="address">2840 N. Ridgeline Ave. Ste.B<br>Van Nuys, CA 91406</span>
      </li>
    </ul>
  </section>

  <section class="card card-back" aria-label="Card back">
    <h2 class="wordmark">Summit BladeAir</h2>
    <p class="services">Airport · Tour guide · Heliport</p>
  </section>
</main>
</body>
</html>
```